A unique communication angle to crowdfunding

Looking for a fresh redesign of a crowd funding website that deals in real estate. I already have the content, but am looking to take the design to the next level.

Existing real estate crowd funding sites focus on the real estate. I want to explore communication angle that:
- puts the investor in the centre of the communication: "become a baron"
- highlights the international nature (international properties, international investors)

There's also quite a lot of copy on the site, as we need to explain the service in quite a bit of detail. There's room to reduce the copy and replace with graphics. Could also consider clicking to see different text (see our difference section in http://galleonfairs.com)

The backend of the platform is already being worked on by a specialist crowd funding service provider.

In total there are 5 pages to be designed.

The homepage is really important. Right now it looks quite dated. It doesn't have a great layout. Note there is no mobile version of the website, so the pages need to be seen well on mobile devices. When looking at the brief, refer to the following links too:

current website:
http://pennyduke.com

some revisions made so far:
http://preview.stakeharbor.com/7K3LQ9

Attached are logo files and another file which contained copy for the pages. No need to rework the logo.

Please make sure to use the same copy in the brief on the webpages, to ensure the layouts work. Designers are free to propose images they feel work on the pages.

I would like to see if rather than tweaking the pages, it's possible to come up with a better design concept. If the 5 pages are accepted, there's a chance I'll request an additional 4 pages.
Updates

Please note the font used in the logo is called "harabara" in case you decide to use it in any of the titles, etc.

Please note there is one additional page for which we would like to review designs. Note the page would be a template to be used on all future real estate detail pages. Here is an example of the current design for reference:

http://pennyduke.com/projects/view/14

In total there are 5 page designs required, (homepage + 4)

Thank you

FYI -

Just a quick note to give information from similar UK real estate crowdfunding sites:
http://www.housewalrus.co.uk
http://tiderock.co.uk
https://www.fundquarry.com

Of the above, only tiderock has a nice clean looking landing page. Information is clear and well laid out.

Hi all, just uploaded a new file in the brief. Contains some comments and a website reference. I thought it may help to explain how we could convey international aspect as well as how we could convey images in a more modern way. This is an option you can consider, but its entirely up to you how how answer the brief. Thanks!

Reason: As requested by some designers needing more time to complete their work. Continue to share your work in progress and receive timely feedback before the deadline.

We would like to let you know that we have just shortlisted the best designs. Together with that, we have also passed some detailed feedback to all designers who weren't shortlisted. If we didn't contact you, please let us know. If you haven't submitted a design or are working on revisions, please note these will no longer be taken into account now. We hope you understand that we need to close the project today. Thank you all once again for your great work and design concepts. Here's hoping we meet again on a future design brief. Cheers, pennyduke team.

Target Market(s)

At the moment, only rich are able to buy real estate. With this service, anyone can become a landlord. Target buyers:

Young professionals, looking to diversify from stock market and lower risk
People nearing retirement, looking for stable rental incomes
Retirees - looking to supplement pensions with possibility of capital gains
Parents - looking for a way to save long term for their children (instead of low interest paying bank accounts)

Industry/Entity Type

Communication

Font styles to use
Sans Serif
Other font styles liked:
• harabara

Colors
add136
f5f9eb
959595
000000

Requirements
Must have
• Overall, the site must convey "whoever you are, you too can become a landlord", and that you don't need to be wealthy to invest in real estate. See

Communication should put the investor (or the baron) at the centre. The investor can be any of those described in the target market.

Show the aspirational side of property ownership.

In addition to the investor/baron character, the second main theme is international. No other real estate crowdfunding website highlights this.
Nice to have
• Banner could show different consumer types, to illustrate that the service can appeal to many different profiles. Refer to attached file "home page reference - plainasbread.com" as an example of how this could be done.

Aim to show the international side of the service. Properties around the world, investors around the world.

```html
<!DOCTYPE html>
<html lang="en">
<head>
<meta charset="utf-8">
<title>pennyduke – Become a baron</title>
<link href="https://fonts.googleapis.com/css2?family=Open+Sans:ital,wght@0,300;0,400;0,600;0,700;0,800;1,700&display=swap" rel="stylesheet">
<style>
:root{
  --green:#add136;
  --green-dark:#8fb121;
  --pale:#f5f9eb;
  --grey:#959595;
  --grey-light:#e6e6e6;
  --grey-mid:#cfcfcf;
  --ink:#000;
  --text:#555;
  --white:#fff;
}
*{box-sizing:border-box;margin:0;padding:0}
html,body{width:1200px;height:4458px;overflow:hidden}
body{font-family:"Open Sans",Arial,sans-serif;color:var(--text);background:var(--white);position:relative}
section,header,footer{position:relative;width:1200px;overflow:hidden}

/* hero */
.hero{height:873px;background:linear-gradient(180deg,#c7ccd2 0%,#aab3bc 45%,#7d8893 75%,#5f6a74 100%)}
.hero-photo{position:absolute;inset:0}
.site-nav{position:absolute;top:0;left:0;width:1200px;height:96px;display:flex;align-items:center;padding:0 32px;background:rgba(0,0,0,.18)}
.brand{display:flex;align-items:center;gap:12px;font-weight:700;font-size:30px;color:var(--green)}
.brand-dot{width:26px;height:26px;border-radius:50%;background:var(--green)}
.nav-links{display:flex;gap:24px;margin-left:28px;list-style:none}
.nav-links li{color:var(--white);font-size:15px;font-weight:700;text-transform:uppercase;white-space:nowrap}
.social{margin-left:auto;display:flex;gap:10px}
.social span{width:30px;height:30px;border-radius:50%;border:2px solid var(--white)}
.hero-title{position:absolute;top:572px;left:0;width:1200px;text-align:center;color:var(--white);text-transform:uppercase}
.hero-title .light{display:block;font-weight:300;font-size:44px;letter-spacing:1px}
.hero-title .bold{display:block;font-weight:700;font-size:40px;letter-spacing:1px}
.hero-down{position:absolute;top:700px;left:556px}
.hero-dots{position:absolute;top:820px;left:0;width:1200px;display:flex;justify-content:center;gap:12px}
.hero-dots span{width:11px;height:11px;border-radius:50%;background:rgba(255,255,255,.55)}
.hero-dots span.on{background:var(--white)}

/* mission band */
.mission{height:323px;background:var(--green);text-align:center;color:var(--white);padding-top:30px}
.mission-icon{display:block;margin:0 auto 14px}
.mission h2{font-size:32px;font-weight:700;font-style:italic;margin-bottom:8px}
.mission p{font-size:20px;line-height:28px;width:900px;margin:0 auto}

/* actions */
.actions{height:271px;background:var(--grey-light);display:flex;justify-content:center;gap:60px;padding-top:68px}
.action{display:flex;gap:22px;width:470px}
.action-tile{flex:0 0 118px;height:128px;background:#6d6d6d;color:var(--white);font-size:11px;text-transform:uppercase;text-align:center;padding-top:16px;line-height:14px}
.action-tile svg{display:block;margin:0 auto 10px}
.action h3{font-size:32px;font-weight:400;color:#777;margin-top:6px}
.action p{font-size:19px;line-height:25px;color:#777}

/* projects */
.projects{height:539px;background:var(--pale);text-align:center;padding-top:34px}
.section-title{color:var(--green);font-size:34px;font-weight:700}
.section-sub{font-size:19px;line-height:26px;color:#777;width:760px;margin:4px auto 0}
.section-sub em{color:var(--green);font-style:normal}
.cards{display:flex;justify-content:center;gap:22px;margin-top:28px}
.card{width:298px;height:330px;background:var(--white);text-align:left;box-shadow:0 2px 4px rgba(0,0,0,.12)}
.card-photo{height:110px;position:relative}
.card-tag{position:absolute;top:16px;left:10px;background:#2c5a8a;color:var(--white);font-size:10px;font-weight:700;padding:2px 6px}
.card-price{position:absolute;top:0;right:0;background:var(--green);color:var(--white);font-weight:700;font-size:15px;padding:6px 12px}
.card-body{padding:10px 12px}
.card h4{color:var(--green-dark);font-size:15px;font-weight:700}
.card p{font-size:12px;line-height:16px;color:#666;margin-top:4px;height:64px}
.bar{height:18px;background:var(--grey-light);margin-top:14px}
.bar i{display:block;height:100%;background:var(--green)}
.funded{font-size:13px;margin-top:12px;color:#555}
.more{display:block;font-size:13px;color:var(--green-dark);margin-top:14px;padding-top:10px;border-top:1px solid var(--grey-light)}

/* community */
.community{height:1802px;background:var(--white);text-align:center;padding-top:52px}
.band{width:594px;height:44px;line-height:44px;margin:0 auto;background:var(--green);color:var(--white);font-size:20px}
.map{position:relative;width:1000px;height:360px;margin:20px auto 0;background:linear-gradient(180deg,#c4c4c4,#a9a9a9)}
.map-pins{position:absolute;inset:0}
.community .band.first{margin-top:40px}
.donut-wrap{position:relative;width:800px;height:490px;margin:30px auto 0}
.donut-label{position:absolute;font-size:19px;color:#555}
.donut-note{font-size:18px;line-height:25px;color:#777;width:620px;margin:6px auto 0}
.community .band.gap{margin-top:32px}

/* press */
.press{height:175px;border-top:1px solid var(--grey-light);display:flex;align-items:center;justify-content:center;gap:28px;padding-top:20px}
.press small{font-size:12px;color:#777;position:absolute;left:64px;top:38px}
.press span{width:118px;height:40px;background:var(--grey-mid)}

/* footer */
.site-footer{height:475px;background:var(--ink);color:#a0a0a0;padding:20px 64px 0}
.footer-top{display:flex;justify-content:space-between;align-items:flex-start}
.footer-top p{width:720px;font-size:13px;line-height:18px}
.group-name{font-size:42px;font-weight:700;color:var(--white);line-height:44px;text-align:right}
.group-name small{display:block;font-size:26px;font-weight:400;color:var(--white)}
.legal{margin-top:38px;font-size:12.5px;line-height:17px}
.legal p+p{margin-top:14px}
.footer-bar{position:absolute;left:0;bottom:0;width:1200px;height:54px;background:#6f6f6f;color:var(--white);font-size:17px;display:flex;align-items:center;justify-content:center;gap:8px}
.footer-bar i{width:24px;height:24px;border-radius:50%;border:2px solid var(--white)}
</style>
</head>
<body>

<header class="hero">
  <div class="hero-photo" role="img" aria-label="Hand holding a model house above a city skyline"></div>
  <nav class="site-nav">
    <div class="brand"><span class="brand-dot"></span>pennyduke</div>
    <ul class="nav-links">
      <li>Home</li><li>Sign in</li><li>How it works</li><li>Discover a project</li><li>The Baron blog</li><li>Find out more</li>
    </ul>
    <div class="social"><span></span><span></span></div>
  </nav>
  <h1 class="hero-title"><span class="light">Property buying</span><span class="bold">is stressful, outdated and in need of change.</span></h1>
  <svg class="hero-down" width="88" height="88" viewBox="0 0 88 88"><circle cx="44" cy="44" r="40" fill="#000" stroke="#fff" stroke-width="4"/><path d="M26 36 L44 54 L62 36" fill="none" stroke="#fff" stroke-width="7"/></svg>
  <div class="hero-dots"><span class="on"></span><span></span><span></span><span></span></div>
</header>

<section class="mission">
  <svg class="mission-icon" width="80" height="80" viewBox="0 0 80 80"><circle cx="40" cy="40" r="37" fill="none" stroke="#fff" stroke-width="4"/><path d="M26 26 L54 54 M54 26 L26 54" stroke="#fff" stroke-width="6" stroke-linecap="round"/></svg>
  <h2>Reconstructing a property ladder that's strong and fair</h2>
  <p>By harnessing the power of crowds, it's possible to become a landlord in locations around the world. Forget the burden of financing 100% of the purchase. Leave the day to day management of your property portfolio to us. Start with 1% in a project and plan your steps to becoming a true baron.</p>
</section>

<section class="actions">
  <div class="action">
    <div class="action-tile"><svg width="58" height="58" viewBox="0 0 58 58"><circle cx="29" cy="29" r="26" fill="none" stroke="#fff" stroke-width="3"/><path d="M24 18 L35 29 L24 40" fill="none" stroke="#fff" stroke-width="4"/></svg>Sign up<br>to buy</div>
    <div><h3>Find properties</h3><p>Sign up to browse the portfolio. Your journey to becoming a real estate baron starts here.</p></div>
  </div>
  <div class="action">
    <div class="action-tile"><svg width="58" height="58" viewBox="0 0 58 58"><circle cx="29" cy="29" r="26" fill="none" stroke="#fff" stroke-width="3"/><path d="M24 18 L35 29 L24 40" fill="none" stroke="#fff" stroke-width="4"/></svg>Submit<br>a property</div>
    <div><h3>Find buyer</h3><p>Submit a property or development and raise funds from our real estate barons.</p></div>
  </div>
</section>

<section class="projects">
  <h2 class="section-title">Featured Projects</h2>
  <p class="section-sub">Brief details of new and popular projects. To view full listings, you will be required to sign up and <em>become a member</em>.</p>
  <div class="cards">
    <article class="card">
      <div class="card-photo" role="img" aria-label="Riverside apartment building" style="background:linear-gradient(180deg,#6f93b8,#3d5a73)"><span class="card-tag">NEW MATCH</span><span class="card-price">From GBP 5,000</span></div>
      <div class="card-body"><h4>14 Harbour Row LONDON E1</h4><p>A landmark development in E1 offering panoramic views across the river Thames less than 2 miles from the City and Docklands Quay.</p><div class="bar"><i style="width:0"></i></div><div class="funded">0% funded</div><span class="more">See Project Details</span></div>
    </article>
    <article class="card">
      <div class="card-photo" role="img" aria-label="Residential tower at dusk" style="background:linear-gradient(180deg,#4b6486,#1f2d44)"><span class="card-tag">NEW MATCH</span><span class="card-price">From GBP 5,270</span></div>
      <div class="card-body"><h4>Cobalt Tower, London E14</h4><p>At the heart of New Larkspur Wharf, a premium residential project by award winning developer Marlowe Build.</p><div class="bar"><i style="width:4%"></i></div><div class="funded">4% funded</div><span class="more">See Project Details</span></div>
    </article>
    <article class="card">
      <div class="card-photo" role="img" aria-label="Island development on the river at night" style="background:linear-gradient(180deg,#3a4f6a,#16202e)"><span class="card-tag">NEW MATCH</span><span class="card-price">From GBP 750</span></div>
      <div class="card-body"><h4>Riverside Isle London E14</h4><p>A new island for London – introducing London's new serviced location from the multi-award winning developer Marlowe Build.</p><div class="bar"><i style="width:51%"></i></div><div class="funded">51% funded</div><span class="more">See Project Details</span></div>
    </article>
  </div>
</section>

<section class="community">
  <h2 class="section-title">Be Part of a Growing International Community</h2>
  <p class="section-sub">Gain access to new projects in world class cities and join our growing community of international landlords.</p>

  <div class="band first">A community of international property barons</div>
  <div class="map" role="img" aria-label="World map showing where pennyduke members live">
    <svg class="map-pins" width="1000" height="360" viewBox="0 0 1000 360">
      <g fill="#add136" stroke="#fff" stroke-width="3">
        <circle cx="180" cy="58" r="25"/><circle cx="250" cy="115" r="25"/><circle cx="140" cy="168" r="25"/><circle cx="310" cy="258" r="25"/>
        <circle cx="470" cy="66" r="25"/><circle cx="520" cy="172" r="25"/><circle cx="610" cy="95" r="25"/><circle cx="720" cy="134" r="25"/>
        <circle cx="820" cy="76" r="25"/><circle cx="880" cy="288" r="25"/>
      </g>
    </svg>
  </div>

  <div class="band gap">Collective buying power of the pennyduke community</div>
  <div class="donut-wrap">
    <svg width="800" height="490" viewBox="0 35 800 490">
      <circle cx="320" cy="280" r="210" fill="none" stroke="#add136" stroke-width="70"/>
      <circle cx="320" cy="280" r="210" fill="none" stroke="#959595" stroke-width="70" stroke-dasharray="208.5 1319.5" transform="rotate(-90 320 280)"/>
      <circle cx="320" cy="280" r="150" fill="#add136"/>
      <text x="320" y="262" fill="#fff" font-family="Open Sans, sans-serif" font-size="40" text-anchor="middle">* USD</text>
      <text x="320" y="318" fill="#fff" font-family="Open Sans, sans-serif" font-size="50" font-weight="700" text-anchor="middle">$2.06m</text>
      <line x1="470" y1="100" x2="560" y2="100" stroke="#959595" stroke-width="2"/>
      <line x1="530" y1="330" x2="560" y2="330" stroke="#959595" stroke-width="2"/>
    </svg>
    <span class="donut-label" style="left:572px;top:51px">Invested 15.8%</span>
    <span class="donut-label" style="left:572px;top:281px">Pledged 84.2%</span>
  </div>
  <p class="donut-note">* Graphic shows the combined USD$ amount invested in projects and pledged from aspiring pennyduke barons</p>

  <div class="band gap">Attractive real estate from around the world</div>
  <div class="map" role="img" aria-label="World map showing locations of listed properties">
    <svg class="map-pins" width="1000" height="360" viewBox="0 0 1000 360">
      <g fill="#add136" stroke="#fff" stroke-width="3">
        <circle cx="160" cy="86" r="25"/><circle cx="230" cy="190" r="25"/><circle cx="330" cy="285" r="25"/><circle cx="480" cy="58" r="25"/>
        <circle cx="500" cy="190" r="25"/><circle cx="640" cy="86" r="25"/><circle cx="760" cy="162" r="25"/><circle cx="860" cy="105" r="25"/>
        <circle cx="900" cy="275" r="25"/>
      </g>
    </svg>
  </div>
</section>

<section class="press">
  <small>Featured in</small>
  <span></span><span></span><span></span><span></span><span></span><span></span><span></span>
</section>

<footer class="site-footer">
  <div class="footer-top">
    <p>pennyduke is part of the Hollow Oak Group. The Hollow Oak Group is a worldwide pioneer and leader in the crowd investing, peer to peer and online investment market.</p>
    <div class="group-name">hollow oak<small>group</small></div>
  </div>
  <div class="legal">
    <p>By accessing this site and any pages thereof, you agree to be bound by the terms and conditions. This website is only suitable, intended and available for professional or sophisticated investors, or to those who are members of the pennyduke community and familiar with the risks associated with private real estate participation. pennyduke does not endorse any of the projects that appear on this website, nor does it make any recommendation regarding the appropriateness of particular opportunities for any participant. Each potential participant must review and evaluate the projects in its or her own discretion and determine the suitability of participating.</p>
    <p>This website (the "Site") is in every respect unaffiliated with any site to which it links or any company or entity listed. Investment opportunity or similar featured on this Site, and is not meant as an endorsement of any of those companies or entities ("third parties"). Furthermore and for the avoidance of doubt, pennyduke Limited is in no way affiliated with any third parties featured or referenced on this Site. There is no commercial relationship between pennyduke Limited and such third parties, nor an agency arrangement or similar. If you believe your content has been reproduced on this Site without permission, please refer to our Terms of Service for information on how to request its removal from the Site.</p>
  </div>
  <div class="footer-bar">© pennyduke 2014 | Follow pennyduke on <i></i><i></i></div>
</footer>

</body>
</html>
```